Letter head / email signature/ contract document templates

We need a professional email signature and letterhead designed for our established carpentry and maintenance company. Our Logo (attached) was originally designed 6 years ago by design guru and we love it, looking for something to compliment it ( not a home job)

```html
<!DOCTYPE html>
<html lang="en">
<head>
<meta charset="utf-8">
<title>Harbourline Joinery – Email Signature &amp; Letterhead</title>
<link href="https://fonts.googleapis.com/css2?family=Questrial&display=swap" rel="stylesheet">
<style>
  :root {
    --brand-red: #e62129;
    --ink: #3b3b3b;
    --muted: #6a6a6a;
    --rule: #777777;
    --paper: #ffffff;
    --backdrop: #e4e4e4;
  }
  * { box-sizing: border-box; margin: 0; padding: 0; }
  html, body {
    width: 830px; height: 1200px; overflow: hidden;
    background: var(--backdrop);
    font-family: "Questrial", "Century Gothic", sans-serif;
    color: var(--ink);
  }
  .sheet {
    position: absolute;
    background: var(--paper);
    box-shadow: 0 4px 14px rgba(0,0,0,.18);
    overflow: hidden;
  }
  .email-signature { left: 111px; top: 74px; width: 609px; height: 154px; }
  .letterhead { left: 110px; top: 269px; width: 611px; height: 857px; }

  .brand {
    position: absolute;
    display: flex; align-items: center; gap: 7px;
  }
  .brand-mark { width: 11px; height: 11px; background: var(--brand-red); flex: none; }
  .brand-name {
    font-size: 19px; line-height: 1.05; color: var(--ink);
    letter-spacing: .2px;
  }
  .email-signature .brand { left: 22px; top: 56px; }
  .letterhead .brand { left: 21px; top: 30px; }

  .signature-divider {
    position: absolute; left: 166px; top: 35px;
    width: 1px; height: 83px; background: var(--brand-red);
  }
  .signature-details { position: absolute; left: 176px; top: 36px; }
  .person-name { font-size: 15px; color: var(--brand-red); line-height: 1; }
  .person-role { font-size: 8.5px; color: var(--muted); margin-top: 3px; }

  .contact-list { list-style: none; }
  .contact-list li {
    display: flex; align-items: center; gap: 5px;
    font-size: 10.5px; color: var(--ink); height: 15px; white-space: nowrap;
  }
  .signature-details .contact-list { margin-top: 8px; }
  .contact-icon { width: 9px; height: 9px; flex: none; }

  .letterhead .contact-list { position: absolute; left: 416px; top: 18px; }
  .letterhead-rule {
    position: absolute; left: 165px; top: 73px;
    width: 430px; height: 1px; background: var(--rule);
  }

  .accent-band { position: absolute; left: 0; }
  .email-signature .accent-band { top: 0; width: 609px; height: 154px; }
  .letterhead .accent-band { top: 0; width: 611px; height: 857px; }
</style>
</head>
<body>

<svg width="0" height="0" style="position:absolute" aria-hidden="true">
  <defs>
    <symbol id="icon-phone" viewBox="0 0 10 10">
      <circle cx="5" cy="5" r="5" fill="#e62129"/>
      <path d="M3.2 2.6c.3-.2.6-.2.8.1l.4.7c.1.2 0 .4-.1.5l-.3.3c.3.6.7 1 1.3 1.3l.3-.3c.1-.1.3-.2.5-.1l.7.4c.3.2.3.5.1.8-.4.5-1 .6-1.6.3C4.3 6.1 3.9 5.7 3.4 4.7c-.3-.7-.7-1.6-.2-2.1z" fill="#fff"/>
    </symbol>
    <symbol id="icon-mail" viewBox="0 0 10 10">
      <circle cx="5" cy="5" r="5" fill="#e62129"/>
      <rect x="2.6" y="3.3" width="4.8" height="3.4" fill="#fff"/>
      <path d="M2.6 3.3 5 5.2 7.4 3.3" fill="none" stroke="#e62129" stroke-width=".6"/>
    </symbol>
    <symbol id="icon-home" viewBox="0 0 10 10">
      <circle cx="5" cy="5" r="5" fill="#e62129"/>
      <path d="M5 2.3 7.4 4.4V7.5H2.6V4.4z" fill="#fff"/>
      <rect x="4.3" y="5.3" width="1.4" height="2.2" fill="#e62129"/>
    </symbol>
  </defs>
</svg>

<section class="sheet email-signature" aria-label="Email signature">
  <svg class="accent-band" viewBox="0 0 609 154" aria-hidden="true">
    <path d="M0 139 H552 Q555 139 557 137 L570 123" fill="none" stroke="#e62129" stroke-width="3.2" stroke-linecap="round"/>
  </svg>
  <div class="brand">
    <span class="brand-mark"></span>
    <span class="brand-name">Harbourline<br>Joinery</span>
  </div>
  <div class="signature-divider"></div>
  <div class="signature-details">
    <p class="person-name">JOHN DOE</p>
    <p class="person-role">Manager</p>
    <ul class="contact-list">
      <li><svg class="contact-icon"><use href="#icon-phone"/></svg>555-014-270</li>
      <li><svg class="contact-icon"><use href="#icon-mail"/></svg>info@harbourlinejoinery.com</li>
      <li><svg class="contact-icon"><use href="#icon-home"/></svg>Your address, your city, box 88900</li>
    </ul>
  </div>
</section>

<section class="sheet letterhead" aria-label="Letterhead">
  <div class="brand">
    <span class="brand-mark"></span>
    <span class="brand-name">Harbourline<br>Joinery</span>
  </div>
  <ul class="contact-list">
    <li><svg class="contact-icon"><use href="#icon-phone"/></svg>555-014-270</li>
    <li><svg class="contact-icon"><use href="#icon-mail"/></svg>info@harbourlinejoinery.com</li>
    <li><svg class="contact-icon"><use href="#icon-home"/></svg>Your address, your city, box 88900</li>
  </ul>
  <div class="letterhead-rule"></div>
  <svg class="accent-band" viewBox="0 0 611 857" aria-hidden="true">
    <path d="M0 806 H448 Q454 806 459 801 L504 755" fill="none" stroke="#e62129" stroke-width="13" stroke-linejoin="round"/>
  </svg>
</section>

</body>
</html>
```